We have a cheerleading competition on Sunday the 30 and I want to encourage parent assistance, support and participation!
Updates

1. Please add:
    Cheer Championship (instead of Cheerleading Competition)

2. Banner: Let's support our Cheerleaders!

Under Banner have the Date in big

Before the Location add:  Joins us at:

Thank you all for your designs and taking the time to submit them. I greatly appreciate them and they were all lovely. I could only pick one though! Hope to have you again on my next project.

Regards, Ramona

Industry/Entity Type

It Support

Requirements
Must have
• Flyer should be 1/2 of an A4 page. kid friendly. The cheerleaders are 6-13 yrs old.
The colors Burgundy, Gold (yellow) and White - It should have the team Eagle design on it. Dorrel Creek Ravens

Simple design. It will contain an address, times and dates.

should have all of the following information:

Date: Sunday - October 30th 2011
Location: Halvern Crest Arena at the Tolliver Ridge College
3872 Pellham Lane
Brindle Harbor, FL 33972
Time: Tickets on sale 8:30AM - Doors Open 9:00AM Starts: 10:00AM
Prices: Adults $10.00 Children $5.00 - Cash Only

```html
<!DOCTYPE html>
<html lang="en">
<head>
<meta charset="utf-8">
<title>Cheerleading Competition Flyer</title>
<link rel="stylesheet" href="https://fonts.googleapis.com/css2?family=Poppins:wght@400;600&display=swap">
<style>
  :root {
    --burgundy: #7d0f1f;
    --burgundy-dark: #6a0a18;
    --gold: #f2b631;
    --gold-deep: #e39a28;
    --gold-light: #f7d35c;
    --white: #ffffff;
    --mist: #f3f2f2;
    --rule: #9a2a38;
  }
  * { margin: 0; padding: 0; box-sizing: border-box; }
  html, body { width: 1200px; height: 849px; overflow: hidden; background: var(--white); }
  .flyer {
    position: relative;
    width: 1200px;
    height: 849px;
    overflow: hidden;
    background: var(--white);
    font-family: "Poppins", Arial, sans-serif;
    color: var(--burgundy);
  }
  .mascot-watermark {
    position: absolute;
    left: 0; top: 20px;
    width: 730px; height: 700px;
    border-radius: 46% 54% 40% 60% / 50% 45% 55% 50%;
    background: radial-gradient(ellipse at 40% 40%, var(--mist) 0%, #f7f6f6 55%, rgba(255,255,255,0) 75%);
  }
  .team-mark {
    position: absolute;
    left: 40px; top: 60px;
    width: 300px;
    display: flex;
    align-items: center;
    gap: 14px;
  }
  .team-mark .dot {
    width: 38px; height: 38px;
    border-radius: 50%;
    background: var(--burgundy);
    flex: none;
  }
  .team-mark .name {
    font-weight: 600;
    font-size: 26px;
    line-height: 1.15;
    color: var(--burgundy);
  }
  .headline {
    position: absolute;
    left: 356px; top: 44px;
    font-size: 61px;
    line-height: 1;
    letter-spacing: -0.5px;
    color: var(--burgundy);
    white-space: nowrap;
  }
  .headline .strong { font-weight: 600; }
  .headline .light { font-weight: 400; }
  .headline-rule {
    position: absolute;
    left: 345px; top: 139px;
    width: 815px; height: 2px;
    background: linear-gradient(90deg, var(--rule), var(--rule) 75%, rgba(154,42,56,0.35));
  }
  .details {
    position: absolute;
    left: 90px; top: 278px;
    list-style: none;
  }
  .detail { position: relative; padding-left: 66px; margin-bottom: 18px; }
  .detail::before {
    content: "";
    position: absolute;
    left: 6px; top: 6px;
    width: 26px; height: 26px;
    border-radius: 50%;
    background: var(--burgundy);
  }
  .detail-label { font-weight: 600; font-size: 25px; line-height: 36px; }
  .detail-text { font-weight: 400; font-size: 25px; line-height: 41px; }
  .cheerleader {
    position: absolute;
    background: linear-gradient(180deg, var(--burgundy) 0%, var(--burgundy-dark) 100%);
  }
  .cheerleader.small {
    left: 625px; top: 505px;
    width: 160px; height: 210px;
    border-radius: 45% 45% 30% 30%;
  }
  .cheerleader.large {
    left: 880px; top: 310px;
    width: 320px; height: 452px;
    border-radius: 40% 40% 4px 4px;
  }
  .accent-stripe {
    position: absolute;
    left: 0; top: 742px;
    width: 1200px; height: 20px;
    background: linear-gradient(90deg, var(--gold-deep), var(--gold) 40%, var(--gold-light));
  }
  .price-band {
    position: absolute;
    left: 0; top: 762px;
    width: 1200px; height: 87px;
    background: var(--burgundy);
    display: flex;
    align-items: center;
    justify-content: center;
    color: var(--white);
    font-size: 29px;
    white-space: nowrap;
  }
  .price-band b { font-weight: 600; }
  .price-band span { padding: 0 8px; }
</style>
</head>
<body>
<main class="flyer">
  <div class="mascot-watermark" role="img" aria-label="Faint oversized team mascot head in the background"></div>

  <div class="team-mark">
    <span class="dot"></span>
    <span class="name">Dorrel Creek<br>Ravens</span>
  </div>

  <h1 class="headline"><span class="strong">cheerleading</span> <span class="light">competition</span></h1>
  <div class="headline-rule"></div>

  <ul class="details">
    <li class="detail">
      <div class="detail-label">Date:</div>
      <div class="detail-text">Sunday - October 30th 2011</div>
    </li>
    <li class="detail">
      <div class="detail-label">Location:</div>
      <div class="detail-text">Halvern Crest Arena at the Tolliver Ridge College<br>3872 Pellham Lane<br>Brindle Harbor, FL 33972</div>
    </li>
    <li class="detail">
      <div class="detail-label">Time:</div>
      <div class="detail-text">Tickets on sale 8:30AM<br>Doors Open 9:00AM<br>Starts: 10:00AM</div>
    </li>
  </ul>

  <div class="cheerleader small" role="img" aria-label="Burgundy silhouette of a jumping cheerleader with pom-poms"></div>
  <div class="cheerleader large" role="img" aria-label="Large burgundy silhouette of a cheerleader raising pom-poms"></div>

  <div class="accent-stripe"></div>
  <footer class="price-band">
    <b>Prices:</b><span>Adults $10.00 Children $5.00</span><b>- Cash Only</b>
  </footer>
</main>
</body>
</html>
```